PowerPoint Presentation 10 Slides Needed with custom graphics and possibly animated gifs

I'm creating an educational webinar for professionals. I have 10 slides that need special treatment--effective visuals that really Deliverables10 PowerPoint slides in shared PPT fileWith 10 or more images that communicate the message described in the slides notes for each slide.DeadlineSlides will be used in a PowerPoint presentation Monday, Dec 10.Due date is Friday, Dec 7.Design GuidanceSee attached deck for existing design template/theme (with colors/logo)You should match the designAnimations should be delivered as GIF files that can appear in a slideAnimation can last 4 to 10 seconds.Instead of animations, photos from Framebarrel can be recommended (I have an account and can provide the final file to use).

```html
<!DOCTYPE html>
<html lang="en">
<head>
<meta charset="utf-8">
<title>Do You Like My Cookie?</title>
<link href="https://fonts.googleapis.com/css2?family=Bebas+Neue&family=Open+Sans:wght@400;600&display=swap" rel="stylesheet">
<style>
  :root {
    --bg: #ffffff;
    --brand-blue: #1f3f9a;
    --brand-green: #1c7a3a;
    --cookie: #c98a4b;
  }
  html, body {
    margin: 0;
    padding: 0;
    overflow: hidden;
    background: var(--bg);
  }
  .slide {
    position: relative;
    width: 1200px;
    height: 669px;
    overflow: hidden;
    background: var(--bg);
  }
  .accent-bar {
    position: absolute;
    left: 0;
    top: 202px;
    width: 33px;
    height: 286px;
    background: var(--brand-green);
  }
  .headline {
    position: absolute;
    left: 100px;
    top: 194px;
    margin: 0;
    font-family: "Bebas Neue", "Oswald", sans-serif;
    font-weight: 400;
    font-size: 116px;
    line-height: 98px;
    letter-spacing: 1px;
    color: var(--brand-blue);
  }
  .tagline {
    position: absolute;
    left: 660px;
    top: 220px;
    width: 414px;
    margin: 0;
    text-align: center;
    font-family: "Open Sans", sans-serif;
    font-size: 24px;
    line-height: 39px;
    color: var(--brand-green);
  }
  .cookie-bubbles {
    position: absolute;
    left: 690px;
    top: 310px;
    width: 400px;
    height: 250px;
  }
  .brand-lockup {
    position: absolute;
    right: 56px;
    top: 50px;
    display: flex;
    align-items: center;
    gap: 22px;
  }
  .series-name {
    font-family: "Bebas Neue", "Oswald", sans-serif;
    font-size: 19px;
    line-height: 17px;
    color: var(--brand-blue);
    width: 70px;
  }
  .company {
    display: flex;
    align-items: center;
    gap: 8px;
    font-family: "Open Sans", sans-serif;
    font-weight: 600;
    font-size: 20px;
    color: var(--brand-green);
  }
  .company-dot {
    width: 14px;
    height: 14px;
    border-radius: 50%;
    background: var(--brand-green);
  }
</style>
</head>
<body>
  <main class="slide">
    <header class="brand-lockup">
      <div class="series-name">Start From Zero</div>
      <div class="company"><span class="company-dot"></span>Patronly</div>
    </header>

    <div class="accent-bar"></div>

    <h1 class="headline">Do You<br>Like My<br>Cookie?</h1>

    <p class="tagline">Imaging communication is<br>like sharing a cookie…</p>

    <svg class="cookie-bubbles" viewBox="0 0 400 250" role="img" aria-label="Two speech bubbles filled with chocolate chip cookie photography">
      <path fill="var(--cookie)" d="M12 166 C12 128 45 98 88 96 C110 95 128 100 142 108 L165 90 L160 120 C172 134 178 150 178 166 C178 206 140 234 95 234 C50 234 12 206 12 166 Z"/>
      <path fill="var(--cookie)" d="M184 98 C184 48 228 14 282 14 C336 14 380 48 380 98 C380 146 336 182 282 182 C262 182 244 178 230 170 L212 184 L216 160 C196 144 184 122 184 98 Z"/>
    </svg>
  </main>
</body>
</html>
```